verdant terraces simple classy business card design

my name is colin barrow and I run a gardening business aimed at high class verdant terraces. the business name is verdant terraces and our logo was designed on pixel harbour .My clientel are anything from residential homes to businesses. I take pride in my work and know that I offer a service like no other in my area.
The business card will be used to represent my business and I want it to be not only rememberable, but simplistic and modern. Eye catching too. Of course I would like it relatable to gardening and appealing to the correct clientel - those being garden enthusiasts, prestigious homes and businesses that are after top of the line gardening services like no other on the market.
I am not a typical lawn mowing business so I don't want a typical card design that represents that. The gardens I work with are generally million dollar properties with owners who are very garden proud looking for upkeep and guidance from me along with sometimes whole new garden designs. I want the business cards to show to my clients that I take pride, as they do, in their garden. And I want them to know from my card that I am a professional, qualified horticulturist offering them a top of the line service for life. I want them to refer my business on. I want them to look at my business card and see class and professionalism in a modern unique bold way.
The card should be simple with the possibility of the logo on the front being embossed/debossed and my details on the back the card should have a organic garden feel it's very important to me that it is absolutely perfect
I am also very open to ideas and suggestions so look forward to seeing the designs. the business logo has been supplied with this project and I want the card to be double sided

Contact info is
Colin Barrow - Managing Director / Horticulturist
Phone : 0481 526 704
Email: colinbarrow@verdantterraces.example.au

Target Market(s)

high class gardens residential and commercial

Industry/Entity Type

Gardener

Contact Information for Business Card

Contact info is
Phone : 0481 526 704

PLEASE MAKE CARD DOUBLE SIDED

Requirements
Must have
• organic simple classy modern feel
• must flow with the current logo that has been supplied with this project
• Double sided
• Must explain in a simple way that I deal with high end gardens and I'm a qualified horticulturist
Nice to have
• embossed debossed logo
Should not have
• shouldn't be to busy or cheap looking

```html
<!DOCTYPE html>
<html lang="en">
<head>
<meta charset="utf-8">
<title>Verdant Terraces – Business Card</title>
<link href="https://fonts.googleapis.com/css2?family=Arimo:wght@400;500&family=Cinzel:wght@400&display=swap" rel="stylesheet">
<style>
  :root {
    --backdrop: #d9dadc;
    --card-light: #eeeff1;
    --brand-green: #52884a;
    --ink: #2f3133;
    --ink-soft: #4a4d50;
    --divider: #b9bcbf;
    --on-green: #f2f4f0;
  }
  * { box-sizing: border-box; margin: 0; padding: 0; }
  html, body {
    width: 1105px;
    height: 1200px;
    overflow: hidden;
    background: var(--backdrop);
  }
  .canvas { position: relative; width: 1105px; height: 1200px; }

  .card {
    position: absolute;
    left: 182px;
    width: 747px;
    height: 425px;
  }
  .card--details { top: 119px; background: var(--card-light); }
  .card--brand { top: 637px; background: var(--brand-green); }

  .edge-tab {
    position: absolute;
    top: 105px;
    width: 12px;
    height: 218px;
    background: var(--brand-green);
  }
  .edge-tab--left { left: 0; border-radius: 0 6px 6px 0; }
  .edge-tab--right { right: 0; border-radius: 6px 0 0 6px; }

  .brand-lockup {
    position: absolute;
    display: flex;
    flex-direction: column;
    align-items: center;
    font-family: "Cinzel", serif;
    font-weight: 400;
  }
  .brand-mark { border-radius: 50%; }
  .brand-name { line-height: 1; text-transform: uppercase; }

  .card--details .brand-lockup {
    left: 45px; top: 100px; width: 260px;
    color: var(--brand-green);
  }
  .card--details .brand-mark {
    width: 66px; height: 66px;
    background: var(--brand-green);
    margin-bottom: 14px;
  }
  .card--details .brand-name--primary { font-size: 38px; letter-spacing: 0.06em; }
  .card--details .brand-name--secondary {
    font-size: 21px; letter-spacing: 0.62em; margin-top: 4px; padding-left: 0.62em;
  }

  .card--brand .brand-lockup {
    left: 0; top: 108px; width: 100%;
    color: var(--on-green);
  }
  .card--brand .brand-mark {
    width: 108px; height: 108px;
    background: var(--on-green);
    margin-bottom: 18px;
  }
  .card--brand .brand-name--primary { font-size: 50px; letter-spacing: 0.05em; }
  .card--brand .brand-name--secondary {
    font-size: 27px; letter-spacing: 0.95em; margin-top: 6px; padding-left: 0.95em;
  }

  .divider {
    position: absolute;
    left: 330px; top: 133px;
    width: 1px; height: 160px;
    background: var(--divider);
  }

  .contact {
    position: absolute;
    left: 355px; top: 133px;
    font-family: "Arimo", sans-serif;
    color: var(--ink);
  }
  .contact__name {
    font-size: 24px; font-weight: 500;
    color: var(--brand-green);
    line-height: 1.2;
  }
  .contact__role { font-size: 19px; margin-top: 4px; line-height: 1.2; }
  .contact__list { list-style: none; margin-top: 22px; }
  .contact__item {
    display: flex; align-items: center;
    font-size: 17px; color: var(--ink-soft);
    height: 29px;
  }
  .contact__icon { width: 17px; height: 17px; margin-right: 12px; flex: none; }

  .web-address {
    position: absolute;
    left: 0; width: 100%; top: 362px;
    text-align: center;
    font-family: "Arimo", sans-serif;
    font-size: 18px;
    letter-spacing: 0.17em;
    color: var(--on-green);
  }
</style>
</head>
<body>
<main class="canvas">

  <section class="card card--details" aria-label="Card front with contact details">
    <span class="edge-tab edge-tab--left"></span>
    <span class="edge-tab edge-tab--right"></span>

    <div class="brand-lockup">
      <span class="brand-mark"></span>
      <span class="brand-name brand-name--primary">Verdant</span>
      <span class="brand-name brand-name--secondary">Terraces</span>
    </div>

    <span class="divider"></span>

    <div class="contact">
      <p class="contact__name">Colin Barrow</p>
      <p class="contact__role">Managing Director / Horticulturist</p>
      <ul class="contact__list">
        <li class="contact__item">
          <svg class="contact__icon" viewBox="0 0 24 24" aria-hidden="true">
            <path fill="#52884a" d="M3 8c0-3 3-5 9-5s9 2 9 5v2h-5V8c-1-1-7-1-8 0v2H3zM7 11h10l3 4v5H4v-5zm5 2a3 3 0 100 6 3 3 0 000-6z"/>
          </svg>
          0481 526 704
        </li>
        <li class="contact__item">
          <svg class="contact__icon" viewBox="0 0 24 24" aria-hidden="true">
            <path fill="#52884a" d="M2 5h20v14H2zm2 2v1l8 5 8-5V7l-8 5z"/>
          </svg>
          colinbarrow@verdantterraces.example.au
        </li>
        <li class="contact__item">
          <svg class="contact__icon" viewBox="0 0 24 24" aria-hidden="true">
            <circle cx="12" cy="12" r="10" fill="#52884a"/>
            <path fill="#eeeff1" d="M7 6c2 1 3 3 2 5s1 3 3 3 1 3 0 5c-3-1-6-4-6-7 0-2 0-4 1-6zm8-1c2 1 3 3 3 5-1 0-2 0-3-1s-1-3 0-4z"/>
          </svg>
          verdantterraces.example.au
        </li>
      </ul>
    </div>
  </section>

  <section class="card card--brand" aria-label="Card back with brand name">
    <div class="brand-lockup">
      <span class="brand-mark"></span>
      <span class="brand-name brand-name--primary">Verdant</span>
      <span class="brand-name brand-name--secondary">Terraces</span>
    </div>
    <p class="web-address">www.verdantterraces.example.au</p>
  </section>

</main>
</body>
</html>
```